"Kestrava Inc." Needs a Logo Design and Business Card

The name of the company is "Kestrava Inc."
Our Business decription, which should appear on the front of the Business Card along with the logo and business name is:
"Boutique Global Procurement and Management Services"
We offer the following SERVICES that should be listed on the back of the Business Card :
"Consultants"
"Management"
"Business Research & Development"
"Sourcing Agent"
"Distributors"
We would like to see designs that use the colors
burnt orange and,
stainless steel
Business card designs should be innovatively modern and contemporary
Telephone number and email address should be on the back of the card
The name of the firm is "Kestrava Inc.
Industry/Entity Type
Steel
Look and feel
Each slider illustrates characteristics of the customer's brand and the style your logo design should communicate.

```html
<!DOCTYPE html>
<html lang="en">
<head>
<meta charset="utf-8">
<title>Kestrava Inc. — Business Card Front</title>
<link rel="stylesheet" href="https://fonts.googleapis.com/css2?family=Poiret+One&family=Questrial&display=swap">
<style>
  :root {
    --charcoal: #333333;
    --burnt-orange: #ff6735;
    --steel-dark: #4d4d4d;
    --steel-veil: rgba(110, 110, 110, 0.45);
    --steel-line: #8a8a8a;
    --band-shade: rgba(0, 0, 0, 0.33);
    --band-shade-deep: rgba(0, 0, 0, 0.5);
    --name-silver: #d2d2d2;
    --ampersand-rust: #5a3227;
  }
  html, body {
    margin: 0;
    padding: 0;
    width: 1200px;
    height: 720px;
    overflow: hidden;
    background: var(--charcoal);
  }
  .card {
    display: block;
    width: 1200px;
    height: 720px;
  }
  .card-bg { fill: var(--charcoal); }
  .pill-orange { fill: var(--burnt-orange); }
  .pill-steel { fill: var(--steel-dark); }
  .pill-steel-veil { fill: var(--steel-veil); }
  .steel-rule { stroke: var(--steel-line); stroke-width: 2; fill: none; }
  .name-band { fill: var(--band-shade); }
  .name-band-deep { fill: var(--band-shade-deep); }
  .company-name {
    font-family: "Poiret One", sans-serif;
    font-size: 56px;
    fill: var(--name-silver);
    letter-spacing: 1px;
  }
  .tagline {
    font-family: "Poiret One", sans-serif;
    font-size: 36px;
    fill: var(--burnt-orange);
  }
  .ampersand {
    font-family: "Questrial", sans-serif;
    font-size: 160px;
    fill: var(--ampersand-rust);
  }
</style>
</head>
<body>
<svg class="card" viewBox="0 0 1200 720" xmlns="http://www.w3.org/2000/svg" aria-label="Kestrava Inc. business card front">
  <defs>
    <clipPath id="clip-orange-pills">
      <rect x="70" y="150" width="270" height="420" rx="135"/>
      <rect x="470" y="60" width="260" height="420" rx="130"/>
    </clipPath>
  </defs>

  <rect class="card-bg" width="1200" height="720"/>

  <rect class="pill-orange" x="70" y="150" width="270" height="420" rx="135"/>
  <rect class="pill-steel" x="375" y="420" width="140" height="240" rx="70"/>
  <rect class="pill-orange" x="470" y="60" width="260" height="420" rx="130"/>
  <rect class="pill-steel-veil" x="780" y="20" width="360" height="500" rx="180"/>
  <line class="steel-rule" x1="755" y1="40" x2="755" y2="500"/>

  <rect class="name-band" x="0" y="246" width="1200" height="67"/>
  <rect class="name-band-deep" x="0" y="246" width="1200" height="67" clip-path="url(#clip-orange-pills)"/>

  <text class="company-name" x="1097" y="304" text-anchor="end">KESTRAVA Inc.</text>

  <text class="ampersand" x="664" y="636">&amp;</text>
  <text class="tagline" x="1096" y="574" text-anchor="end">Boutique Global Procurement</text>
  <text class="tagline" x="1096" y="618" text-anchor="end">Management Services</text>
</svg>
</body>
</html>
```